Commit To Be The Best! - Marketing, Training, Managment for Multifamily Professionals

Flyer for training event. I have to be able to edit location, times, speakers, cost,
We will have 2 to 4 speakers for each event. Each event may have a different topic relating to the main topic (Marketing, Training, Management). The idea is to get as many people to open or pick up the fly and say "I have to attend" this seminar. We are the experts in the industry and want to portray this with the flyer. Each speaker will have a topic and a certain amount of time. Each topic will be different.
Updates

Project Deadline Extended
Reason: I apologize for the new design deadline. I've been traveling extensively for work and unable to view submissions. Currently I am not traveling and able to dedicate time to view all of the wonderful submissions. I'm looking forward to selecting one. Thank you all for your understanding.

Target Market(s)

Multifamily - Apartment Communities, Owners, Apartment Associations, Leasing Agents, Marketing Directors, Managers, Presidents,

Industry/Entity Type

Marketing

Colors

Designer to choose colors to be used in the design.

Requirements
Must have
• Editable flyer. I have to be able to edit; location, times/date, speaker, cost, description.
• Sponsored by KTV Power attached Logo for KTV
Nice to have
• Spot for photo of each speaker (2-4) speaker

```html
<!DOCTYPE html>
<html lang="en">
<head>
<meta charset="utf-8">
<title>Training Event Flyer</title>
<link href="https://fonts.googleapis.com/css2?family=Roboto+Condensed:wght@300;400;700;800&display=swap" rel="stylesheet">
<style>
  :root {
    --page-bg: #e4e4e4;
    --paper: #ffffff;
    --brand-blue: #213b93;
    --ink: #151515;
    --muted-ink: #3a3a3a;
    --rule-grey: #6f6f6f;
    --avatar-dark: #2d3650;
    --avatar-light: #c9ced8;
  }
  * { box-sizing: border-box; margin: 0; padding: 0; }
  html, body { width: 1200px; height: 966px; overflow: hidden; }
  body {
    background: var(--page-bg);
    font-family: "Roboto Condensed", "Arial Narrow", sans-serif;
    color: var(--ink);
  }
  .flyer {
    position: absolute;
    left: 258px;
    top: 0;
    width: 683px;
    height: 966px;
    background: var(--paper);
    overflow: hidden;
  }
  .hero-art { position: absolute; left: 0; top: 0; width: 683px; height: 600px; }
  .event-label {
    position: absolute;
    left: 36px;
    top: 34px;
    font-weight: 800;
    font-size: 64px;
    letter-spacing: 1px;
    color: var(--brand-blue);
    line-height: 1;
  }
  .event-title {
    position: absolute;
    left: 0;
    width: 683px;
    top: 486px;
    text-align: center;
    font-weight: 700;
    font-size: 62px;
    line-height: 1;
    color: var(--ink);
  }
  .event-meta {
    position: absolute;
    left: 0;
    width: 683px;
    top: 556px;
    text-align: center;
    font-weight: 700;
    font-size: 20px;
    line-height: 1;
    color: var(--brand-blue);
  }
  .event-meta .sep { color: var(--rule-grey); margin: 0 10px; }
  .section-rule {
    position: absolute;
    left: 0;
    top: 593px;
    width: 683px;
    height: 4px;
    background: var(--rule-grey);
  }
  .speakers {
    position: absolute;
    left: 22px;
    top: 616px;
    width: 640px;
    display: flex;
    justify-content: space-between;
  }
  .speaker { width: 150px; text-align: center; }
  .speaker-photo {
    width: 112px;
    height: 112px;
    margin: 0 auto 10px;
    border-radius: 50%;
    border: 2px solid var(--ink);
    background: linear-gradient(180deg, #eef1f4 0%, #d3d8e0 45%, var(--avatar-dark) 100%);
  }
  .speaker-name { font-weight: 400; font-size: 17px; color: var(--muted-ink); }
  .speaker-topic { font-weight: 700; font-size: 21px; margin-top: 2px; }
  .speaker-detail { font-weight: 400; font-size: 17px; color: var(--muted-ink); line-height: 1.2; }
  .sponsor {
    position: absolute;
    right: 38px;
    top: 836px;
    text-align: right;
  }
  .sponsor-label { font-weight: 700; font-size: 12px; color: var(--ink); }
  .sponsor-name {
    font-weight: 700;
    font-size: 40px;
    line-height: 1;
    color: var(--ink);
    display: flex;
    align-items: center;
    gap: 8px;
    justify-content: flex-end;
  }
  .sponsor-name .dot { width: 12px; height: 12px; background: var(--brand-blue); }
  .tagline {
    position: absolute;
    left: 38px;
    top: 852px;
    font-weight: 700;
    font-size: 50px;
    line-height: 1;
    color: var(--brand-blue);
  }
  .thanks {
    position: absolute;
    left: 140px;
    top: 910px;
    font-weight: 400;
    font-size: 26px;
    color: var(--ink);
  }
</style>
</head>
<body>
  <main class="flyer">
    <svg class="hero-art" viewBox="0 0 683 600" xmlns="http://www.w3.org/2000/svg">
      <defs>
        <linearGradient id="photoTone" x1="0" y1="0" x2="0.35" y2="1">
          <stop offset="0" stop-color="#e3e8ee"/>
          <stop offset="0.3" stop-color="#b9c1c9"/>
          <stop offset="0.55" stop-color="#4a4d57"/>
          <stop offset="0.75" stop-color="#a98456"/>
          <stop offset="1" stop-color="#d2a86c"/>
        </linearGradient>
        <linearGradient id="bandTone" x1="0" y1="0" x2="1" y2="0">
          <stop offset="0" stop-color="#f3f4f5"/>
          <stop offset="1" stop-color="#e6e9ec"/>
        </linearGradient>
      </defs>
      <rect role="img" aria-label="Faint background image of presenters at flip charts" x="0" y="380" width="683" height="213" fill="url(#bandTone)"/>
      <path role="img" aria-label="Photo of a trainer leading a group seated around a conference table" d="M0 0 H683 V400 Q360 440 0 510 Z" fill="url(#photoTone)"/>
      <path d="M0 510 Q360 440 683 400" fill="none" stroke="#6f6f6f" stroke-width="5"/>
    </svg>

    <h1 class="event-label">TRAINING EVENT</h1>
    <h2 class="event-title">Title Here</h2>
    <p class="event-meta">Date Here<span class="sep">|</span>Cost Here</p>
    <div class="section-rule"></div>

    <section class="speakers">
      <article class="speaker">
        <div class="speaker-photo" role="img" aria-label="Speaker 1 portrait"></div>
        <p class="speaker-name">Speaker-1</p>
        <p class="speaker-topic">Topic Here</p>
        <p class="speaker-detail">Location</p>
        <p class="speaker-detail">Times</p>
      </article>
      <article class="speaker">
        <div class="speaker-photo" role="img" aria-label="Speaker 2 portrait"></div>
        <p class="speaker-name">Speaker-2</p>
        <p class="speaker-topic">Topic Here</p>
        <p class="speaker-detail">Location</p>
        <p class="speaker-detail">Times</p>
      </article>
      <article class="speaker">
        <div class="speaker-photo" role="img" aria-label="Speaker 3 portrait"></div>
        <p class="speaker-name">Speaker-3</p>
        <p class="speaker-topic">Topic Here</p>
        <p class="speaker-detail">Location</p>
        <p class="speaker-detail">Times</p>
      </article>
      <article class="speaker">
        <div class="speaker-photo" role="img" aria-label="Speaker 4 portrait"></div>
        <p class="speaker-name">Speaker-4</p>
        <p class="speaker-topic">Topic Here</p>
        <p class="speaker-detail">Location</p>
        <p class="speaker-detail">Times</p>
      </article>
    </section>

    <div class="sponsor">
      <p class="sponsor-label">Sponsored by</p>
      <p class="sponsor-name">KTV<span class="dot"></span></p>
    </div>

    <p class="tagline">Commit To Be The Best</p>
    <p class="thanks">Thanks For Your Interest</p>
  </main>
</body>
</html>
```